Professional Package for CPA Firm

We would like a stationery design for our new CPA Firm based in Atlanta, GA called 'Vale 8'. We work with investors to help grow investments, tax free. We would like the design to have a professional/minimal look with a 'wow' factor. We need 9.5″ x 4.125″, 9x12, and 10x13 mailing envelopes, business cards, and a letterhead. We have a logo that is already complete. For the letterhead, we would like to have space to put credentials at the bottom of the page

Industry/Entity Type

CPA, Accounting

```html
<!DOCTYPE html>
<html lang="en">
<head>
<meta charset="utf-8">
<title>Vale 8 Stationery Package</title>
<link href="https://fonts.googleapis.com/css2?family=Lato:wght@300;400;700;900&family=Great+Vibes&display=swap" rel="stylesheet">
<style>
:root{
  --stage:#959595;
  --ink:#000000;
  --paper:#ffffff;
  --blue:#0a9ad8;
  --text:#3a3a3a;
  --muted:#5a5a5a;
  --rule:#8a8a8a;
  --label:#1c1c1c;
  --sig-tone:#dbe9f5;
}
*{box-sizing:border-box;margin:0;padding:0}
html,body{width:1200px;height:680px;overflow:hidden;background:var(--stage)}
body{position:relative;font-family:'Lato',Arial,sans-serif;color:var(--text)}
.piece{position:absolute;background:var(--paper);overflow:hidden}
.label{position:absolute;font-size:9.5px;letter-spacing:.2px;color:var(--label);text-transform:uppercase;transform:translateX(-50%);white-space:nowrap}
.brand{font-family:'Lato',Arial,sans-serif;font-weight:900;color:var(--paper);line-height:1;white-space:nowrap}
.brand-sub{color:var(--paper);font-weight:400;letter-spacing:.4px;white-space:nowrap}
.tagline{font-family:'Great Vibes',cursive;white-space:nowrap}
.icon{display:inline-block;vertical-align:middle;margin-right:4px;fill:var(--blue)}
.contact-line{white-space:nowrap}

/* Letterhead */
.letterhead{left:66px;top:47px;width:391px;height:553px}
.letterhead .band{position:absolute;left:0;top:0;width:100%;height:95px;background:var(--ink)}
.letterhead .lockup{position:absolute;left:35px;top:36px}
.letterhead .lockup .brand{font-size:22px}
.letterhead .lockup .brand-sub{font-size:5px;margin-top:3px}
.letterhead .divider{position:absolute;left:266px;top:23px;width:1px;height:52px;background:var(--rule)}
.letterhead .contacts{position:absolute;left:282px;top:23px;color:var(--paper);font-size:6.6px;line-height:8.9px}
.letterhead .contacts .icon{width:5px;height:5px;margin-right:3px}
.letterhead .salutation{position:absolute;left:35px;top:156px;font-size:10px;font-weight:300;color:var(--text)}
.letterhead .body{position:absolute;left:35px;top:186px;width:325px;font-size:5.3px;line-height:8.4px;color:var(--muted);text-align:justify}
.letterhead .body p{margin-bottom:8.4px}
.letterhead .closing{position:absolute;left:35px;top:364px;font-size:5.6px;color:var(--muted)}
.letterhead .signature{position:absolute;left:33px;top:383px;width:68px;height:32px;background:linear-gradient(90deg,var(--sig-tone),#eef4fa)}
.letterhead .tagline{position:absolute;left:106px;top:515px;font-size:14px;color:#333}

/* Envelope */
.envelope-back{left:490px;top:47px;width:354px;height:160px}
.envelope-back .flap{position:absolute;left:0;top:0;width:100%;height:60px;background:var(--blue);border-radius:0 0 14px 14px;clip-path:polygon(0 0,100% 0,97% 100%,3% 100%);}
.envelope-back .brand{position:absolute;left:0;width:100%;top:13px;text-align:center;font-size:13px}
.envelope-back .tagline{position:absolute;left:0;width:100%;top:33px;text-align:center;font-size:10px;color:var(--paper)}
.envelope-front{left:543px;top:132px;width:356px;height:162px;box-shadow:0 1px 3px rgba(0,0,0,.25)}
.envelope-front .band{position:absolute;left:0;top:0;width:100%;height:62px;background:var(--ink)}
.envelope-front .lockup{position:absolute;left:19px;top:33px}
.envelope-front .lockup .brand{font-size:13px}
.envelope-front .lockup .brand-sub{font-size:3.4px;margin-top:2px}
.envelope-front .return{position:absolute;left:19px;top:72px;font-size:7px;line-height:9px;color:var(--text)}

/* Business cards */
.card-front{left:944px;top:48px;width:186px;height:106px}
.card-front .who{position:absolute;right:92px;top:41px;text-align:right;font-size:3.6px;line-height:5px;color:var(--muted);white-space:nowrap}
.card-front .who .name{font-size:5.8px;line-height:7px;font-weight:700;color:var(--blue)}
.card-front .divider{position:absolute;left:99px;top:42px;width:.6px;height:22px;background:var(--rule)}
.card-front .contacts{position:absolute;left:104px;top:43px;font-size:3.6px;line-height:5.2px;color:var(--muted)}
.card-front .contacts .icon{width:3px;height:3px;margin-right:2px}
.card-back{left:944px;top:182px;width:193px;height:110px;background:var(--ink)}
.card-back .lockup{position:absolute;left:0;width:100%;top:49px;text-align:center}
.card-back .lockup .brand{font-size:15px}
.card-back .lockup .brand-sub{font-size:4px;margin-top:2px}
.card-back .tagline{position:absolute;left:0;width:100%;top:83px;text-align:center;font-size:9px;color:var(--paper)}

/* Email signatures */
.sig .logo-block{position:absolute;left:0;top:0;background:var(--ink);display:flex;flex-direction:column;align-items:center;justify-content:flex-end}
.sig .name{font-size:15px;color:var(--blue);font-weight:400;line-height:1.1;white-space:nowrap}
.sig .role{font-size:9px;color:var(--text);line-height:1.2}
.sig .lines{font-size:9px;line-height:11.5px;color:var(--muted);white-space:nowrap}
.sig .lines .icon{width:6px;height:6px}
.sig .vrule{position:absolute;width:1px;background:#9a9a9a}

.sig-one{left:490px;top:334px;width:175px;height:265px}
.sig-one .logo-block{width:100%;height:97px;padding-bottom:15px}
.sig-one .logo-block .brand{font-size:24px}
.sig-one .logo-block .brand-sub{font-size:5.6px;margin-top:4px}
.sig-one .name{position:absolute;left:27px;top:109px}
.sig-one .role{position:absolute;left:28px;top:126px}
.sig-one .short-rule{position:absolute;left:29px;width:14px;height:1px;background:var(--rule)}
.sig-one .address{position:absolute;left:29px;top:158px}
.sig-one .contacts{position:absolute;left:29px;top:198px}

.sig-two{left:695px;top:334px;width:455px;height:141px}
.sig-two .logo-block{width:139px;height:100%;padding-bottom:37px}
.sig-two .logo-block .brand{font-size:22px}
.sig-two .logo-block .brand-sub{font-size:5.4px;margin-top:4px}
.sig-two .name{position:absolute;left:161px;top:46px}
.sig-two .role{position:absolute;left:162px;top:63px}
.sig-two .address{position:absolute;left:162px;top:78px}
.sig-two .vrule{left:297px;top:48px;height:48px}
.sig-two .contacts{position:absolute;left:318px;top:50px}

.sig-three{left:695px;top:513px;width:455px;height:87px}
.sig-three .logo-block{width:102px;height:100%;padding-bottom:16px}
.sig-three .logo-block .brand{font-size:18px}
.sig-three .logo-block .brand-sub{font-size:4.4px;margin-top:3px}
.sig-three .who{position:absolute;left:118px;width:80px;top:33px;text-align:center}
.sig-three .name{font-size:13.5px}
.sig-three .vrule.first{left:212px;top:29px;height:32px}
.sig-three .address{position:absolute;left:226px;top:27px}
.sig-three .vrule.second{left:334px;top:29px;height:32px}
.sig-three .contacts{position:absolute;left:351px;top:27px}
</style>
</head>
<body>

<svg width="0" height="0" style="position:absolute">
  <defs>
    <symbol id="i-phone" viewBox="0 0 10 10"><path d="M2.2 0.6 L3.9 2.6 L3 3.7 C3.6 5 4.9 6.3 6.2 7 L7.3 6 L9.4 7.8 L8.3 9.4 C4.4 9 1 5.6 0.6 1.7 Z"/></symbol>
    <symbol id="i-mobile" viewBox="0 0 10 10"><path d="M2.8 0 H7.2 A0.8 0.8 0 0 1 8 0.8 V9.2 A0.8 0.8 0 0 1 7.2 10 H2.8 A0.8 0.8 0 0 1 2 9.2 V0.8 A0.8 0.8 0 0 1 2.8 0 Z M3.2 1.2 V8 H6.8 V1.2 Z"/></symbol>
    <symbol id="i-mail" viewBox="0 0 10 10"><path d="M0 2 H10 V8 H0 Z M0.6 2.4 L5 5.6 L9.4 2.4 V2.6 L5 6.2 L0.6 2.6 Z" fill-rule="evenodd"/></symbol>
    <symbol id="i-web" viewBox="0 0 10 10"><circle cx="5" cy="5" r="4.6"/><path d="M3 3 L5 2 L6 4 L4.5 6 L6 8 L4 8.5 L3 6 Z" fill="#ffffff" opacity=".6"/></symbol>
  </defs>
</svg>

<!-- Letterhead -->
<section class="piece letterhead">
  <header class="band">
    <div class="lockup">
      <div class="brand">Vale 8</div>
      <div class="brand-sub">CPAs and Tax Advisors</div>
    </div>
    <div class="divider"></div>
    <div class="contacts">
      <div class="contact-line">4120 Larkspur Drive</div>
      <div class="contact-line">Atlanta, Georgia 30308</div>
      <div class="contact-line"><svg class="icon"><use href="#i-phone"/></svg>555-214-7730</div>
      <div class="contact-line"><svg class="icon"><use href="#i-mobile"/></svg>555-318-2046</div>
      <div class="contact-line"><svg class="icon"><use href="#i-mail"/></svg>info@vale8.com</div>
      <div class="contact-line"><svg class="icon"><use href="#i-web"/></svg>www.vale8.com</div>
    </div>
  </header>
  <p class="salutation">Dear Mr. Reyes,</p>
  <div class="body">
    <p>We are pleased to confirm our engagement for the coming tax year. Our team will review your portfolio, prepare quarterly estimates and identify every lawful way to keep more of your returns working for you. Please gather last year's statements before our first meeting.</p>
    <p>Once we receive your documents, we will outline a plan for retirement accounts, municipal bonds and other tax-advantaged holdings. Each recommendation comes with a clear summary of costs, benefits and timing, so you can decide with confidence and ask questions at any stage.</p>
    <p>Throughout the year we will monitor changes in federal and state rules that may affect your position. When an opportunity appears, your advisor will contact you directly with a brief note and suggested next steps. You may also reach us by phone or email during regular office hours.</p>
    <p>Thank you for choosing our firm. We look forward to helping your investments grow and to building a lasting working relationship with you and your family.</p>
  </div>
  <p class="closing">Sincerely,</p>
  <div class="signature" role="img" aria-label="Handwritten signature of Daniel Hart"></div>
  <p class="tagline">Grow Your Investments Tax-Free</p>
</section>
<div class="label" style="left:268px;top:618px">Letterhead</div>

<!-- Envelope -->
<section class="piece envelope-back">
  <div class="flap">
    <div class="brand">Vale 8</div>
    <div class="tagline">Grow Your Investments Tax-Free</div>
  </div>
</section>
<section class="piece envelope-front">
  <header class="band">
    <div class="lockup">
      <div class="brand">Vale 8</div>
      <div class="brand-sub">CPAs and Tax Advisors</div>
    </div>
  </header>
  <div class="return">4120 Larkspur Drive<br>Atlanta, Georgia 30308</div>
</section>
<div class="label" style="left:723px;top:303px">Envelope</div>

<!-- Business cards -->
<section class="piece card-front">
  <div class="who">
    <div class="name">DANIEL HART</div>
    <div>President</div>
    <div>4120 Larkspur Drive</div>
    <div>Atlanta, Georgia 30308</div>
  </div>
  <div class="divider"></div>
  <div class="contacts">
    <div class="contact-line"><svg class="icon"><use href="#i-phone"/></svg>555-214-7730</div>
    <div class="contact-line"><svg class="icon"><use href="#i-mobile"/></svg>555-402-6619</div>
    <div class="contact-line"><svg class="icon"><use href="#i-mail"/></svg>info@vale8.com</div>
    <div class="contact-line"><svg class="icon"><use href="#i-web"/></svg>www.vale8.com</div>
  </div>
</section>
<div class="label" style="left:1040px;top:163px">Front Card</div>

<section class="piece card-back">
  <div class="lockup">
    <div class="brand">Vale 8</div>
    <div class="brand-sub">CPAs and Tax Advisors</div>
  </div>
  <div class="tagline">Grow Your Investments Tax-Free</div>
</section>
<div class="label" style="left:1040px;top:303px">Back Card</div>

<!-- Email signature 1 -->
<section class="piece sig sig-one">
  <div class="logo-block">
    <div class="brand">Vale 8</div>
    <div class="brand-sub">CPAs and Tax Advisors</div>
  </div>
  <div class="name">Daniel Hart</div>
  <div class="role">President</div>
  <div class="short-rule" style="top:146px"></div>
  <div class="lines address">4120 Larkspur Drive<br>Atlanta, Georgia 30308</div>
  <div class="short-rule" style="top:184px"></div>
  <div class="lines contacts">
    <div><svg class="icon"><use href="#i-phone"/></svg>555-214-7730</div>
    <div><svg class="icon"><use href="#i-mobile"/></svg>555-318-2046</div>
    <div><svg class="icon"><use href="#i-mail"/></svg>info@vale8.com</div>
    <div><svg class="icon"><use href="#i-web"/></svg>www.vale8.com</div>
  </div>
</section>
<div class="label" style="left:581px;top:618px">Email Signature 1</div>

<!-- Email signature 2 -->
<section class="piece sig sig-two">
  <div class="logo-block">
    <div class="brand">Vale 8</div>
    <div class="brand-sub">CPAs and Tax Advisors</div>
  </div>
  <div class="name">Daniel Hart</div>
  <div class="role">President</div>
  <div class="lines address">4120 Larkspur Drive<br>Atlanta, Georgia 30308</div>
  <div class="vrule"></div>
  <div class="lines contacts">
    <div><svg class="icon"><use href="#i-phone"/></svg>555-214-7730</div>
    <div><svg class="icon"><use href="#i-mobile"/></svg>555-318-2046</div>
    <div><svg class="icon"><use href="#i-mail"/></svg>info@vale8.com</div>
    <div><svg class="icon"><use href="#i-web"/></svg>www.vale8.com</div>
  </div>
</section>
<div class="label" style="left:909px;top:487px">Email Signature 2</div>

<!-- Email signature 3 -->
<section class="piece sig sig-three">
  <div class="logo-block">
    <div class="brand">Vale 8</div>
    <div class="brand-sub">CPAs and Tax Advisors</div>
  </div>
  <div class="who">
    <div class="name">Daniel Hart</div>
    <div class="role">President</div>
  </div>
  <div class="vrule first"></div>
  <div class="lines address">4120 Larkspur Drive<br>Atlanta, Georgia 30308<br>www.vale8.com</div>
  <div class="vrule second"></div>
  <div class="lines contacts">
    <div><svg class="icon"><use href="#i-phone"/></svg>555-214-7730</div>
    <div><svg class="icon"><use href="#i-mobile"/></svg>555-318-2046</div>
    <div><svg class="icon"><use href="#i-mail"/></svg>info@vale8.com</div>
  </div>
</section>
<div class="label" style="left:909px;top:618px">Email Signature 3</div>

</body>
</html>
```